Medical VIP club - small design

Please read the specs in a design brief attached. Also we don't have logo in a Vector format and attaching the only version we have.

Club

```html
<!DOCTYPE html>
<html lang="en">
<head>
<meta charset="utf-8">
<title>Veridana – Services</title>
<link rel="stylesheet" href="https://fonts.googleapis.com/css2?family=Arimo:wght@400;700&display=swap">
<style>
  :root {
    --page-bg: #5e4f37;
    --band: #e9dcc4;
    --tab-top: #b3a285;
    --tab-bottom: #7b6b50;
    --tab-green-top: #c2c07a;
    --tab-green-bottom: #8e8b3d;
    --tab-gold-top: #ecc943;
    --tab-gold-bottom: #b28f10;
    --brand: #4a3a22;
    --olive-top: #aaa55a;
    --olive-bottom: #8a8436;
    --rule: #c9c9c9;
    --text: #333333;
    --white: #ffffff;
  }
  * { box-sizing: border-box; margin: 0; padding: 0; }
  html, body { width: 1200px; height: 874px; overflow: hidden; }
  body {
    position: relative;
    background: var(--page-bg);
    font-family: "Arimo", Arial, sans-serif;
    color: var(--text);
  }
  .header {
    position: absolute; left: 24px; top: 10px; width: 1159px; height: 187px;
    border-radius: 14px; overflow: hidden;
    border: 1px solid #d8ccb2;
    background: linear-gradient(180deg, #cfc2a5 0%, #a79373 55%, #7d6b4d 100%);
  }
  .header-scene {
    position: absolute; left: 440px; top: 0; width: 720px; height: 187px;
    background: linear-gradient(90deg, rgba(167,147,115,1) 0%, rgba(120,150,150,0.85) 25%, #5f8f96 45%, #9a8a66 70%, #6c7a55 100%);
  }
  .brand-name {
    position: absolute; left: 44px; top: 62px;
    font-size: 60px; font-weight: 700; color: var(--brand); letter-spacing: -1px;
  }
  .phone-icon { position: absolute; left: 789px; top: 54px; }
  .phone-number {
    position: absolute; left: 912px; top: 76px;
    font-size: 44px; font-weight: 700; color: var(--white);
    text-shadow: 0 0 3px #3a2e1c, 0 2px 3px #3a2e1c;
  }
  .nav-band { position: absolute; left: 0; top: 241px; width: 1200px; height: 38px; background: var(--band); }
  .nav { position: absolute; left: 24px; top: 207px; display: flex; gap: 4px; }
  .nav-tab {
    width: 190px; height: 72px; border-radius: 12px 12px 0 0;
    background: linear-gradient(180deg, var(--tab-top), var(--tab-bottom));
    color: var(--white); font-size: 20px;
    display: flex; align-items: center; justify-content: center;
    border: 1px solid rgba(255,255,255,0.35); border-bottom: none;
  }
  .nav-tab.is-current { background: linear-gradient(180deg, var(--tab-green-top), var(--tab-green-bottom)); }
  .nav-tab.is-highlight { background: linear-gradient(180deg, var(--tab-gold-top), var(--tab-gold-bottom)); }
  .panel {
    position: absolute; left: 18px; top: 288px; width: 1170px; height: 486px;
    background: var(--white); border-radius: 12px; overflow: hidden;
    border: 1px solid #d8ccb2;
  }
  .panel-title {
    height: 55px; padding-left: 31px; line-height: 50px;
    background: linear-gradient(180deg, #a39273, #6d5d42);
    color: var(--white); font-size: 24px;
    box-shadow: 0 4px 6px rgba(0,0,0,0.15);
  }
  .price-table {
    position: absolute; left: 29px; top: 82px; width: 1110px;
    border-collapse: collapse; font-size: 14px;
  }
  .price-table th {
    height: 35px; color: var(--white); font-weight: 700; font-size: 14px;
    background: linear-gradient(180deg, var(--olive-top), var(--olive-bottom));
    border: 1px solid var(--rule);
  }
  .price-table td {
    height: 35.5px; padding-left: 20px; border: 1px solid var(--rule);
  }
  .price-table td:not(:first-child) { padding-left: 14px; }
  .price-table .col-1 { width: 359px; }
  .price-table .col-2 { width: 387px; }
  .price-table .price-row td {
    border: none; text-align: center; padding: 0; height: 44px;
    font-weight: 700; font-family: Georgia, serif; font-size: 14px;
  }
  .footer {
    position: absolute; left: 18px; top: 781px; width: 1170px; height: 85px;
    border-radius: 12px; border: 1px solid #d8ccb2;
    background: linear-gradient(180deg, #ffffff 0%, #e6dac4 40%, #ad9a78 100%);
  }
  .social { position: absolute; left: 29px; top: 27px; display: flex; gap: 5px; }
  .social-link { width: 38px; height: 38px; border-radius: 6px; }
  .social-link.is-blue { background: #3b5a98; }
  .social-link.is-sky { background: #3fb0dc; }
  .social-link.is-orange { background: #e3641d; }
  .copyright {
    position: absolute; left: 0; right: 0; top: 38px; text-align: center;
    font-size: 13px; color: #3a2e1c;
  }
  .footer-brand {
    position: absolute; right: 36px; top: 22px;
    font-size: 36px; font-weight: 700; color: var(--brand);
  }
</style>
</head>
<body>
  <header class="header">
    <div class="header-scene" role="img" aria-label="Coastal view of a beach, sea and seaside road"></div>
    <div class="brand-name">Veridana</div>
    <svg class="phone-icon" width="104" height="104" viewBox="0 0 104 104" aria-hidden="true">
      <defs>
        <radialGradient id="coin" cx="40%" cy="35%" r="70%">
          <stop offset="0" stop-color="#e3c48a"/>
          <stop offset="1" stop-color="#8a5f22"/>
        </radialGradient>
      </defs>
      <circle cx="52" cy="52" r="50" fill="url(#coin)" stroke="#f3e4c2" stroke-width="2"/>
      <path d="M26 44 q26 -20 52 0 l-4 8 h-10 l-2 -6 q-10 -4 -20 0 l-2 6 h-10 z" fill="#fff"/>
      <path d="M34 56 h36 l6 18 h-48 z" fill="#fff"/>
      <circle cx="52" cy="64" r="6" fill="#a77a38"/>
    </svg>
    <div class="phone-number">555-010-200</div>
  </header>

  <div class="nav-band"></div>
  <nav class="nav">
    <div class="nav-tab">About Us</div>
    <div class="nav-tab">VIP Club</div>
    <div class="nav-tab is-current">Services</div>
    <div class="nav-tab">Packages &amp; Prices</div>
    <div class="nav-tab is-highlight">Registration</div>
    <div class="nav-tab">Contacts</div>
  </nav>

  <main class="panel">
    <h1 class="panel-title" style="font-weight:400">Services</h1>
    <table class="price-table">
      <thead>
        <tr><th class="col-1">Package 1</th><th class="col-2">Package 2</th><th>Package 3</th></tr>
      </thead>
      <tbody>
        <tr><td>-Lorem ipsum</td><td>-Lorem ipsum</td><td>-Lorem ipsum</td></tr>
        <tr><td>-Lorem ipsum</td><td>-Lorem ipsum</td><td>-Lorem ipsum</td></tr>
        <tr><td>-Lorem ipsum</td><td>-Lorem ipsum</td><td>-Lorem ipsum</td></tr>
        <tr><td>-Lorem ipsum</td><td>-Lorem ipsum</td><td>-Lorem ipsum</td></tr>
        <tr><td>-Lorem ipsum</td><td>-Lorem ipsum</td><td>-Lorem ipsum</td></tr>
        <tr><td>-Lorem ipsum</td><td>-Lorem ipsum</td><td>-Lorem ipsum</td></tr>
        <tr><td>-Lorem ipsum</td><td>-Lorem ipsum</td><td>-Lorem ipsum</td></tr>
        <tr><td>-Lorem ipsum</td><td>-Lorem ipsum</td><td>-Lorem ipsum</td></tr>
        <tr><td>-Lorem ipsum</td><td>-Lorem ipsum</td><td>-Lorem ipsum</td></tr>
        <tr class="price-row"><td>$000</td><td>$000</td><td>$000</td></tr>
      </tbody>
    </table>
  </main>

  <footer class="footer">
    <div class="social">
      <span class="social-link is-blue"></span>
      <span class="social-link is-sky"></span>
      <span class="social-link is-orange"></span>
    </div>
    <p class="copyright">Copyright ©2010 Veridana. All Rights Reserved</p>
    <div class="footer-brand">Veridana</div>
  </footer>
</body>
</html>
```